International business needs business cards

Our company, DRV Ventures Inc. is in the business of supplying a range construction products with particular emphasis on CEMENT. We have developed our own brand - TORVAN SUPPLIES - with which to infiltrate the market. We are launching our brand of cement (TORVAN Type IS Cement) into the Caribbean which is unlike anything this market has ever seen. A monopoly has existed here for the past 60-odd years and the market has now opened to allow the importation of other brands and consumers are anxious and ready for change/improvement. We are very excited to be launching and want to make a great first impression. We will be conducting workshops and seminars (from government level to the hardware store owners) and we want our business card to give us the strong, confident introduction that we need.

Target Market(s)

construction; builders; engineers; home owners

Industry/Entity Type

Construction

Contact Information for Business Card

Marisol Depree
CEO
cell # 1 555 4180736
Ground floor,Lindell Plaza Suite 2734
George Town,Grand Cayman
Cayman Islands,KY1-4823
EMAIL: m.depree@drvventuresinc.example
web site drvventuresinc.example

COMPANY: skype info drv.ventures.example

second card
Yvette Brannock-Depree
CFO
CELL# 1 555 607 3941
George Town,Grand Cayman
Cayman Islands,KY1-4823
EMAIL: y.brannockdepree@drvventuresinc.example
website drvventuresinc.example

Requirements
Must have
• Business cards must display BOTH logos - DRV is the company and TORVAN is the brand.

```html
<!DOCTYPE html>
<html lang="en">
<head>
<meta charset="utf-8">
<title>DRV Ventures Inc. — Business Card</title>
<link rel="stylesheet" href="https://fonts.googleapis.com/css2?family=Open+Sans:wght@400;600;700&display=swap">
<style>
  :root {
    --backdrop: #a3a3a3;
    --card: #eeeff1;
    --maroon: #6e1216;
    --ink: #1c1c1c;
    --text: #4a4a4a;
    --rule: #c9c9cc;
  }
  * { margin: 0; padding: 0; box-sizing: border-box; }
  html, body {
    width: 1105px; height: 1200px; overflow: hidden;
    background: var(--backdrop);
    font-family: "Open Sans", sans-serif;
  }
  .card {
    position: absolute; left: 182px;
    width: 746px; height: 427px;
    background: var(--card);
    overflow: hidden;
  }
  .card--front { top: 119px; }
  .card--back { top: 635px; }

  .brand {
    position: absolute; left: 42px; top: 146px;
    display: flex; align-items: center; gap: 12px;
  }
  .brand__mark { width: 61px; height: 66px; background: var(--maroon); }
  .brand__name { font-size: 23px; font-weight: 700; color: var(--ink); white-space: nowrap; }

  .divider {
    position: absolute; left: 360px; top: 61px;
    width: 1px; height: 296px; background: var(--rule);
  }
  .details { position: absolute; left: 390px; top: 58px; right: 24px; color: var(--text); }
  .details__name { font-size: 27px; font-weight: 600; color: var(--maroon); line-height: 36px; white-space: nowrap; }
  .details__role { font-size: 18px; color: var(--ink); line-height: 26px; margin-bottom: 10px; }
  .details__address { font-size: 18px; line-height: 26px; font-style: normal; margin-bottom: 12px; white-space: nowrap; }
  .contact { list-style: none; font-size: 17px; line-height: 29px; }
  .contact li { display: flex; align-items: center; gap: 9px; white-space: nowrap; }
  .contact svg { width: 16px; height: 16px; flex: none; }

  .band-line {
    position: absolute; left: 0; right: 0; top: 391px;
    height: 3px; background: var(--ink);
  }
  .band {
    position: absolute; left: 0; right: 0; top: 398px; bottom: 0;
    background: var(--maroon);
  }

  .product-brand {
    position: absolute; left: 0; right: 0; top: 185px;
    display: flex; justify-content: center; align-items: center; gap: 14px;
  }
  .product-brand__mark { width: 34px; height: 34px; border-radius: 50%; background: var(--ink); }
  .product-brand__name { font-size: 40px; font-weight: 700; color: var(--ink); letter-spacing: 3px; }
  .back-web {
    position: absolute; left: 0; right: 0; top: 376px;
    text-align: center; font-size: 18px; color: var(--text);
  }
</style>
</head>
<body>
  <section class="card card--front" aria-label="Business card front">
    <div class="brand">
      <span class="brand__mark"></span>
      <span class="brand__name">DRV Ventures Inc.</span>
    </div>
    <div class="divider"></div>
    <div class="details">
      <p class="details__name">Marisol Depree</p>
      <p class="details__role">CEO</p>
      <address class="details__address">
        Ground floor<br>
        Lindell Plaza Suite 2734<br>
        George Town,Grand Cayman<br>
        Cayman Islands,KY1-4823
      </address>
      <ul class="contact">
        <li>
          <svg viewBox="0 0 16 16" aria-hidden="true"><rect x="4" y="1" width="8" height="14" rx="1.5" fill="none" stroke="var(--maroon)" stroke-width="2"/><rect x="7" y="11.5" width="2" height="1.5" fill="var(--maroon)"/></svg>
          1 555 4180736
        </li>
        <li>
          <svg viewBox="0 0 16 16" aria-hidden="true"><rect x="1" y="3" width="14" height="10" fill="var(--maroon)"/><path d="M1 3 L8 9 L15 3" fill="none" stroke="var(--card)" stroke-width="1.3"/></svg>
          m.depree@drvventuresinc.example
        </li>
        <li>
          <svg viewBox="0 0 16 16" aria-hidden="true"><circle cx="8" cy="8" r="7" fill="var(--maroon)"/><path d="M1 8 H15 M8 1 C4 5 4 11 8 15 M8 1 C12 5 12 11 8 15" fill="none" stroke="var(--card)" stroke-width="1"/></svg>
          www.drvventuresinc.example
        </li>
      </ul>
    </div>
    <div class="band-line"></div>
    <div class="band"></div>
  </section>

  <section class="card card--back" aria-label="Business card back">
    <div class="product-brand">
      <span class="product-brand__mark"></span>
      <span class="product-brand__name">TORVAN</span>
    </div>
    <p class="back-web">www.drvventuresinc.example</p>
  </section>
</body>
</html>
```